Cafe Business needs a business card design

I already have an ai logo I would like to use and color. I need someone to make a business card for me on adobe illustrator with it. Its for a cafe restaurant opening in Japan I would like to be able to change out the names, contact info, ect on my own from adobe illustrator.

Industry/Entity Type

Business

Contact Information for Business Card

Double sided with logo on one side and info on the other. Name, Tel, fax, email and west

```html
<!DOCTYPE html>
<html lang="en">
<head>
<meta charset="utf-8">
<title>Kumo Cafe — Business Card</title>
<link href="https://fonts.googleapis.com/css2?family=Montserrat:wght@400;500;700&display=swap" rel="stylesheet">
<style>
  :root {
    --page: #d9d4cb;
    --card: #efebe3;
    --card-shade: #e2ddd3;
    --brown: #5a3821;
    --brown-dark: #4a2d1a;
    --cream-text: #f3eee6;
  }
  * { box-sizing: border-box; margin: 0; padding: 0; }
  html, body { width: 1200px; height: 780px; overflow: hidden; }
  body {
    background: var(--page);
    font-family: "Montserrat", Arial, sans-serif;
    color: var(--brown);
    display: flex;
    align-items: center;
    justify-content: center;
    gap: 40px;
  }
  .card {
    position: relative;
    width: 560px;
    height: 320px;
    background: linear-gradient(135deg, var(--card) 0%, var(--card-shade) 100%);
    box-shadow: 0 6px 18px rgba(60, 40, 20, 0.18);
    overflow: hidden;
  }

  /* Front (info side) */
  .card-front .brand {
    position: absolute;
    left: 44px;
    top: 62px;
    display: flex;
    flex-direction: column;
    align-items: flex-start;
    gap: 14px;
  }
  .brand-square {
    width: 112px;
    height: 112px;
    background: var(--brown);
  }
  .brand-name {
    font-weight: 700;
    font-size: 24px;
    letter-spacing: 1px;
    color: var(--brown);
    white-space: nowrap;
  }
  .divider {
    position: absolute;
    left: 228px;
    top: 44px;
    width: 1.5px;
    height: 186px;
    background: var(--brown);
  }
  .person {
    position: absolute;
    left: 262px;
    top: 50px;
  }
  .person-name { font-weight: 700; font-size: 22px; }
  .person-title { font-size: 13px; margin-top: 2px; }
  .contact-list {
    position: absolute;
    left: 262px;
    top: 128px;
    list-style: none;
    font-size: 15px;
    line-height: 23px;
  }
  .contact-list li { display: flex; align-items: center; gap: 8px; }
  .contact-icon {
    width: 14px;
    height: 14px;
    background: var(--brown);
    border-radius: 2px;
    display: inline-flex;
    align-items: center;
    justify-content: center;
    flex: none;
  }
  .address-band {
    position: absolute;
    left: 0; right: 0; bottom: 0;
    height: 52px;
    background: var(--brown);
    color: var(--cream-text);
    font-size: 15px;
    display: flex;
    align-items: center;
    padding-left: 44px;
  }

  /* Back (logo side) */
  .card-back .brand-lockup {
    position: absolute;
    left: 50%;
    top: 78px;
    transform: translateX(-50%);
    display: flex;
    flex-direction: column;
    align-items: center;
    gap: 12px;
  }
  .card-back .brand-square { width: 100px; height: 100px; }
  .card-back .website {
    position: absolute;
    left: 0; right: 0;
    bottom: 48px;
    text-align: center;
    font-size: 15px;
  }
</style>
</head>
<body>

  <section class="card card-front" aria-label="Business card, information side">
    <div class="brand">
      <div class="brand-square"></div>
      <div class="brand-name">KUMO CAFE</div>
    </div>
    <div class="divider"></div>
    <div class="person">
      <div class="person-name">Employee Name</div>
      <div class="person-title">Director</div>
    </div>
    <ul class="contact-list">
      <li>
        <span class="contact-icon">
          <svg width="10" height="10" viewBox="0 0 10 10"><path d="M2 1 L4 1 L4.6 3 L3.6 3.8 Q4.6 5.6 6.2 6.4 L7 5.4 L9 6 L9 8 Q5 9 2.2 5.2 Q1 3 2 1 Z" fill="#f3eee6"/></svg>
        </span>0123 456 789
      </li>
      <li>
        <span class="contact-icon">
          <svg width="10" height="10" viewBox="0 0 10 10"><rect x="1.5" y="3" width="7" height="5" fill="none" stroke="#f3eee6" stroke-width="1"/><rect x="3" y="1" width="4" height="2" fill="#f3eee6"/></svg>
        </span>0123 456 789
      </li>
      <li>
        <span class="contact-icon">
          <svg width="10" height="10" viewBox="0 0 10 10"><rect x="1" y="2.5" width="8" height="5.5" fill="none" stroke="#f3eee6" stroke-width="1"/><path d="M1 2.5 L5 6 L9 2.5" fill="none" stroke="#f3eee6" stroke-width="1"/></svg>
        </span>hello@kumocafe.jp
      </li>
      <li>
        <span class="contact-icon">
          <svg width="10" height="10" viewBox="0 0 10 10"><circle cx="5" cy="5" r="3.8" fill="none" stroke="#f3eee6" stroke-width="1"/><path d="M1.2 5 H8.8 M5 1.2 V8.8" stroke="#f3eee6" stroke-width="0.8"/></svg>
        </span>www.kumocafe.jp
      </li>
    </ul>
    <div class="address-band">P.O. Box 000, your address New Zealand</div>
  </section>

  <section class="card card-back" aria-label="Business card, logo side">
    <div class="brand-lockup">
      <div class="brand-square"></div>
      <div class="brand-name">KUMO CAFE</div>
    </div>
    <div class="website">www.kumocafe.jp</div>
  </section>

</body>
</html>
```